Bright Path Notes Wordpress Blog

I need to design a WordPress blog page. The name of the Blog is "Bright Path Notes". I am hoping for a simple design that is easy for me to post future posts to. I like the color teal for this. The website is brightpathnotesblog.com where I am going to write a personal blog. I don't have a logo for this, but am hoping for a header that has some swirly, but classy looking text. Easy on the eyes. The website will only have a couple of pages - the home landing page, and an about me page.

Font styles to use
Script

Colors
00a990
86cfc6
cfeae6

Requirements
Must have
• A header for the landing page of the blog. Clean layout of where the blog posts will lie.

```html
<!DOCTYPE html>
<html lang="en">
<head>
<meta charset="utf-8">
<title>Bright Path Notes</title>
<link href="https://fonts.googleapis.com/css2?family=Montserrat:wght@400;500;600;700&family=Lato:wght@400;700&display=swap" rel="stylesheet">
<style>
:root{
  --teal:#1c8c9c;
  --teal-soft:#86cfc6;
  --teal-pale:#cfeae6;
  --ink:#2b2b2b;
  --text:#555;
  --muted:#777;
  --rule:#dcdcdc;
  --band:#f2f2f2;
  --tab:#e8e8e8;
  --coral:#ee6f6f;
  --white:#fff;
}
*{box-sizing:border-box;margin:0;padding:0}
html,body{width:1200px;height:2426px;overflow:hidden;background:var(--white)}
body{position:relative;font-family:'Lato',sans-serif;color:var(--text)}
.abs{position:absolute}

.ornament{left:40px;top:0;width:1120px;height:130px;
  background:radial-gradient(ellipse at 50% 40%,rgba(95,184,196,.55),rgba(134,207,198,.18) 55%,rgba(255,255,255,0) 75%)}
.site-title{left:0;width:1200px;top:163px;text-align:center;font-family:'Montserrat',sans-serif;font-weight:500;font-size:33px;letter-spacing:1.5px;color:#3a3a3a}
.main-nav{left:0;width:1200px;top:237px;display:flex;justify-content:center;gap:54px;font-family:'Montserrat',sans-serif;font-weight:500;font-size:16px;color:#333}
.main-nav svg{margin-top:2px}

.features{left:0;top:291px;width:1200px;height:330px;display:flex}
.feature{width:400px;display:flex;flex-direction:column;border-right:1px solid #ddd}
.feature-head{position:relative;height:92px;background:var(--band);text-align:center;padding-top:22px;font-family:'Montserrat',sans-serif}
.feature-head h2{font-size:19px;font-weight:500;color:#2b2b2b;letter-spacing:.3px}
.feature-head p{font-size:13px;color:#555;margin-top:12px}
.feature-head.pointer::after{content:"";position:absolute;left:50%;bottom:-10px;margin-left:-10px;border:10px solid transparent;border-bottom:0;border-top-color:var(--band)}
.feature-photo{flex:1}
.ph-city{background:linear-gradient(135deg,#8b8f94,#d8d8d8 55%,#6d7176)}
.ph-wall{background:linear-gradient(120deg,#b3784b,#c9c9c9 45%,#9a9a9a)}
.ph-group{background:linear-gradient(120deg,#d69a5a,#b44c3e 40%,#6c8fb0 75%,#e4c9a2)}

.tabs{left:97px;top:668px;display:flex;gap:8px;font-family:'Montserrat',sans-serif;font-size:13px;font-weight:600}
.tab{height:34px;line-height:34px;padding:0 20px;background:var(--tab);color:#555}
.tab.active{background:var(--teal);color:var(--white);width:81px;text-align:center;padding:0}

.post{left:97px;width:566px}
.post h3{font-family:'Montserrat',sans-serif;font-weight:700;font-size:27px;color:var(--ink);line-height:34px}
.byline{font-family:'Montserrat',sans-serif;font-size:19px;color:#555;margin-top:8px}
.byline span{color:var(--teal)}
.meta{margin-top:10px;border-top:1px solid var(--rule);padding-top:12px;display:flex;align-items:center;font-family:'Montserrat',sans-serif;font-size:11px;color:#666}
.meta .m{display:flex;align-items:center;gap:8px}
.meta .m1{width:147px}.meta .m2{width:178px}.meta .m3{width:147px}
.meta .share{display:flex;gap:14px;margin-left:auto;margin-right:6px}
.dot{width:8px;height:8px;border-radius:50%;background:#777;display:inline-block}
.post-photo{width:522px;height:205px;margin-top:24px}
.ph-balloons{background:linear-gradient(120deg,#cdd3b4,#e6dcc4 50%,#c7c9a0)}
.ph-desk{background:linear-gradient(120deg,#a6624a,#cfc2b8 45%,#6b7d8e)}
.ph-couple{background:linear-gradient(120deg,#5a6470,#8e6a52 45%,#3b3f45)}
.excerpt{width:522px;margin-top:20px;font-size:13px;line-height:21px;color:#444}
.read-more{display:inline-block;margin-top:18px;border:1px solid var(--teal);color:var(--teal);font-family:'Montserrat',sans-serif;font-size:11.5px;font-weight:500;letter-spacing:.5px;padding:6px 9px}

.avatar-ring{left:793px;top:706px;width:260px;height:260px;border-radius:50%;border:1.5px dashed var(--teal);padding:10px}
.avatar{width:100%;height:100%;border-radius:50%;background:radial-gradient(circle at 50% 45%,#c99a80,#5a3a2c 70%)}
.author-name{left:745px;width:356px;top:990px;display:flex;align-items:center;gap:18px;font-family:'Montserrat',sans-serif;font-size:24px;color:#333}
.author-name::before,.author-name::after{content:"";flex:1;height:1px;background:var(--rule)}
.author-bio{left:747px;width:354px;top:1041px;font-size:13px;line-height:21px;text-align:justify;text-align-last:center;color:#555}
.author-social{left:745px;width:356px;top:1187px;display:flex;justify-content:center;gap:24px}
.newsletter{left:768px;top:1240px;width:314px;height:26px;border:1px solid #ddd;display:flex;align-items:center;justify-content:space-between;padding:0 6px 0 8px;font-size:11px;color:#444}

.widget{left:747px;width:318px}
.widget h4{font-family:'Montserrat',sans-serif;font-weight:500;font-size:16px;color:#333;padding-bottom:10px;border-bottom:1px solid var(--rule)}
.widget ul{list-style:none;margin-top:14px}
.widget li{position:relative;padding-left:12px;font-size:11.5px;color:#444;line-height:18px}
.widget li::before{content:"";position:absolute;left:0;top:5px;border:4px solid transparent;border-right:0;border-left-color:#444}
.cats li{margin-bottom:11px}
.recent li{margin-bottom:20px;line-height:20px}
.recent .more{font-size:12px;color:var(--teal);margin-top:-6px}
.archives li{margin-bottom:11px}

.ebook{left:747px;top:2167px;width:354px;height:173px;background:var(--coral);text-align:center;color:var(--white);font-family:'Montserrat',sans-serif;padding-top:24px}
.ebook h5{font-size:27px;font-weight:700}
.ebook p{font-size:17px;font-weight:700;line-height:25px;margin-top:14px}
.ebook .share{display:flex;justify-content:center;gap:16px;margin-top:14px}
.ebook .dot{background:var(--white);width:7px;height:7px}

.footer{left:0;top:2380px;width:1200px;height:46px;background:var(--teal);color:var(--white);text-align:center;line-height:46px;font-family:'Montserrat',sans-serif;font-size:11.5px;font-weight:600}
</style>
</head>
<body>

<header>
  <div class="abs ornament" role="img" aria-label="Teal swirling flourish ornament"></div>
  <h1 class="abs site-title">Bright Path Notes</h1>
  <nav class="abs main-nav">
    <span>Home</span><span>About Nora</span><span>Contact</span>
    <svg width="16" height="16" viewBox="0 0 16 16"><circle cx="6.5" cy="6.5" r="5" fill="none" stroke="#333" stroke-width="2"/><line x1="10.2" y1="10.2" x2="15" y2="15" stroke="#333" stroke-width="2.4"/></svg>
  </nav>
</header>

<section class="abs features">
  <div class="feature">
    <div class="feature-head pointer"><h2>BECOME MORE CONFIDENT</h2><p>Setting Goals And Persevering</p></div>
    <div class="feature-photo ph-city" role="img" aria-label="Man in a dark suit standing on a city street"></div>
  </div>
  <div class="feature">
    <div class="feature-head pointer"><h2>IMPROVE YOUR BODY LANGUAGE</h2><p>Make You More Persistent</p></div>
    <div class="feature-photo ph-wall" role="img" aria-label="Bearded man pointing at a grey wall reading How We Behave"></div>
  </div>
  <div class="feature" style="border-right:0">
    <div class="feature-head"><h2>LEARN TO GET ALONG WITH OTHERS</h2><p>Simulating Trust And Closeness</p></div>
    <div class="feature-photo ph-group" role="img" aria-label="Group of smiling friends taking a selfie"></div>
  </div>
</section>

<div class="abs tabs">
  <span class="tab active">NEW</span><span class="tab">Collections</span><span class="tab">Recommended</span><span class="tab">Popular</span>
</div>

<article class="abs post" style="top:749px">
  <h3>Become An Early Riser</h3>
  <p class="byline">By <span>Daniel</span></p>
  <div class="meta">
    <span class="m m1"><svg width="12" height="12" viewBox="0 0 12 12"><circle cx="6" cy="6" r="5" fill="none" stroke="#1c8c9c" stroke-width="1.5"/><path d="M6 3v3h2" stroke="#1c8c9c" stroke-width="1.3" fill="none"/></svg>March 15th,2017</span>
    <span class="m m2"><svg width="10" height="12" viewBox="0 0 10 12"><path d="M1 0h8v12L5 9 1 12z" fill="#1c8c9c"/></svg>Life Goal Development</span>
    <span class="m m3"><svg width="14" height="12" viewBox="0 0 14 12"><ellipse cx="7" cy="5" rx="7" ry="5" fill="#1c8c9c"/><path d="M3 8l-1 4 4-3z" fill="#1c8c9c"/></svg>2 Comments</span>
    <span class="share"><i class="dot"></i><i class="dot"></i><i class="dot"></i></span>
  </div>
  <div class="post-photo ph-balloons" role="img" aria-label="Woman holding pastel balloons against a muted sky"></div>
  <p class="excerpt">Lorem Ipsum is simply dummy text of the printing and typesetting industry. Lorem Ipsum has been the industry's standard dummy text ever since the 1500s, when an unknown printer took a galley of type and scrambled it to make a type specimen book. It has survived not only five centuries, but also the leap into electronic typesetting, remaining essentially unchanged. It was popularised in the 1960s.</p>
  <span class="read-more">READ MORE</span>
</article>

<article class="abs post" style="top:1304px">
  <h3>&nbsp;Overcome Limiting Beliefs</h3>
  <p class="byline">By <span>Daniel</span></p>
  <div class="meta">
    <span class="m m1"><svg width="12" height="12" viewBox="0 0 12 12"><circle cx="6" cy="6" r="5" fill="none" stroke="#1c8c9c" stroke-width="1.5"/><path d="M6 3v3h2" stroke="#1c8c9c" stroke-width="1.3" fill="none"/></svg>March 15th,2017</span>
    <span class="m m2"><svg width="10" height="12" viewBox="0 0 10 12"><path d="M1 0h8v12L5 9 1 12z" fill="#1c8c9c"/></svg>Life Goal Development</span>
    <span class="m m3"><svg width="14" height="12" viewBox="0 0 14 12"><ellipse cx="7" cy="5" rx="7" ry="5" fill="#1c8c9c"/><path d="M3 8l-1 4 4-3z" fill="#1c8c9c"/></svg>2 Comments</span>
    <span class="share"><i class="dot"></i><i class="dot"></i><i class="dot"></i></span>
  </div>
  <div class="post-photo ph-desk" role="img" aria-label="Relaxed man leaning back at his desk"></div>
  <p class="excerpt">Lorem Ipsum is simply dummy text of the printing and typesetting industry. Lorem Ipsum has been the industry's standard dummy text ever since the 1500s, when an unknown printer took a galley of type and scrambled it to make a type specimen book. It has survived not only five centuries, but also the leap into electronic typesetting, remaining essentially unchanged. It was popularised in the 1960s.</p>
  <span class="read-more">READ MORE</span>
</article>

<article class="abs post" style="top:1849px">
  <h3>Become More Mindful</h3>
  <p class="byline">By <span>Daniel</span></p>
  <div class="meta">
    <span class="m m1"><svg width="12" height="12" viewBox="0 0 12 12"><circle cx="6" cy="6" r="5" fill="none" stroke="#1c8c9c" stroke-width="1.5"/><path d="M6 3v3h2" stroke="#1c8c9c" stroke-width="1.3" fill="none"/></svg>March 15th,2017</span>
    <span class="m m2"><svg width="10" height="12" viewBox="0 0 10 12"><path d="M1 0h8v12L5 9 1 12z" fill="#1c8c9c"/></svg>Life Goal Development</span>
  </div>
  <div class="post-photo ph-couple" role="img" aria-label="Smiling couple embracing"></div>
  <p class="excerpt">Lorem Ipsum is simply dummy text of the printing and typesetting industry. Lorem Ipsum has been the industry's standard dummy text ever since the 1500s, when an unknown printer took a galley of type and scrambled it to make a type specimen book. It has survived not only five centuries, but also the leap into electronic typesetting, remaining essentially unchanged. It was popularised in the 1960s.</p>
  <span class="read-more">READ MORE</span>
</article>

<aside>
  <div class="abs avatar-ring"><div class="avatar" role="img" aria-label="Portrait of the blog author"></div></div>
  <div class="abs author-name">Nora</div>
  <p class="abs author-bio">Lorem Ipsum is simply dummy text of the printing and typesetting industry. Lorem Ipsum has been the industry's standard dummy text ever since the 1500s, when an unknown printer took a galley of type and scrambled it to make a type specimen book. It has survived not only five centuries,</p>
  <div class="abs author-social"><i class="dot" style="background:#333"></i><i class="dot" style="background:#333"></i><i class="dot" style="background:#333"></i><i class="dot" style="background:#333"></i></div>
  <div class="abs newsletter">Subscribe Our Newsletter
    <svg width="16" height="14" viewBox="0 0 16 14"><path d="M0 5h7V2l5 5-5 5V9H0z" fill="#1c8c9c"/><path d="M10 1h5v12h-5" fill="none" stroke="#1c8c9c" stroke-width="1.6"/></svg>
  </div>

  <div class="abs widget cats" style="top:1301px">
    <h4>Categories</h4>
    <ul>
      <li>Improve Your Body Language. ...</li>
      <li>Learn to Get Along With Others. ...</li>
      <li>Stop Procrastinating. ...</li>
      <li>Become an Early Riser. ...</li>
      <li>Become More Proactive. ...</li>
      <li>Acquire Conflict Resolution Skills. ...</li>
      <li>Release the Past</li>
    </ul>
  </div>

  <div class="abs widget recent" style="top:1589px">
    <h4>Recent Posts</h4>
    <ul>
      <li>Salary Packaging Basics: How To Manage Your Salary Package March 16, 2017</li>
      <li>Bad Work Habits That Can Cost You Your Job March 15, 2017</li>
      <li>10 Mindfulness Tips For All Employees March 13, 2017</li>
      <li>37 Motivational Workplace Quotes March 9, 201</li>
      <li>10 Mindfulness Tips For All Employees March 13, 2017</li>
    </ul>
    <p class="more">Read More.....</p>
  </div>

  <div class="abs widget archives" style="top:1943px">
    <h4>Archives</h4>
    <ul>
      <li>February 2017</li>
      <li>January 2017</li>
      <li>December 2016</li>
      <li>November 2016</li>
      <li>October 2016</li>
    </ul>
  </div>

  <div class="abs ebook">
    <h5>GET OUR EBOOK</h5>
    <p>CLICK HERE TO DOWNLOAD OUR<br>FULL EBOOOK VERSION</p>
    <div class="share"><i class="dot"></i><i class="dot"></i><i class="dot"></i></div>
  </div>
</aside>

<footer class="abs footer">© 2017 Bright Path Notes. All Rights Reserved.</footer>

</body>
</html>
```